HearthMile business card and stationary design

We are looking for a simple yet elegant design for our mortgage company business card and stationary.

The card should include:
Name (Marcus Pell)
Title (CEO)
Phone Number (732-555-0182)
Address (48 Birchwell Court, Suite 314, Hazlet, NJ 07730)
Email (email@hearthmile.example)
"NMLS" i.e. (NMLS 61947)
"Company NMLS" (Company NMLS 274615)

Contact Information for Business Card

See above

```html
<!DOCTYPE html>
<html lang="en">
<head>
<meta charset="UTF-8">
<title>HearthMile Business Card</title>
<link href="https://fonts.googleapis.com/css2?family=Lexend:wght@300;400;500&family=Oswald:wght@600&display=swap" rel="stylesheet">
<style>
  :root {
    --backdrop: #8a8b8c;
    --card-dark: #121d27;
    --card-dark-edge: #1a2a38;
    --card-light: #e6e6e8;
    --brand-blue: #1a95d4;
    --ink: #1b2530;
    --ink-soft: #2c3540;
  }
  * { margin: 0; padding: 0; box-sizing: border-box; }
  html, body {
    width: 1200px;
    height: 781px;
    overflow: hidden;
    background: var(--backdrop);
    font-family: "Lexend", sans-serif;
  }
  .card {
    position: absolute;
    left: 358px;
    width: 452px;
    height: 251px;
  }
  .card-front {
    top: 103px;
    background: radial-gradient(ellipse at 50% 100%, var(--card-dark-edge) 0%, var(--card-dark) 70%);
    display: flex;
    align-items: center;
    justify-content: center;
  }
  .front-wordmark {
    font-size: 54px;
    font-weight: 500;
    color: var(--brand-blue);
    letter-spacing: -0.5px;
    line-height: 1;
  }
  .card-back {
    top: 408px;
    background: var(--card-light);
    text-align: center;
    color: var(--ink);
  }
  .back-wordmark {
    position: absolute;
    top: 40px;
    left: 0;
    width: 100%;
    font-size: 30px;
    font-weight: 500;
    color: var(--brand-blue);
    letter-spacing: -0.3px;
  }
  .holder-name {
    position: absolute;
    top: 104px;
    left: 0;
    width: 100%;
    font-family: "Oswald", sans-serif;
    font-weight: 600;
    font-size: 27px;
    line-height: 1;
    color: var(--brand-blue);
    letter-spacing: 0.5px;
    text-transform: uppercase;
  }
  .holder-title {
    position: absolute;
    top: 135px;
    left: 0;
    width: 100%;
    font-size: 14px;
    font-weight: 300;
    color: var(--ink);
  }
  .title-rule {
    position: absolute;
    top: 160px;
    left: 212px;
    width: 28px;
    height: 1.5px;
    background: var(--brand-blue);
  }
  .contact-row {
    position: absolute;
    top: 174px;
    left: 0;
    width: 100%;
    display: flex;
    justify-content: center;
    gap: 12px;
    font-size: 13px;
    font-weight: 300;
    color: var(--ink-soft);
  }
  .contact-item { display: flex; align-items: center; gap: 6px; }
  .contact-item svg { width: 12px; height: 12px; }
  .address {
    position: absolute;
    top: 196px;
    left: 0;
    width: 100%;
    font-size: 12.5px;
    font-weight: 300;
    color: var(--ink-soft);
  }
  .licences {
    position: absolute;
    top: 218px;
    left: 0;
    width: 100%;
    font-size: 10px;
    font-weight: 300;
    color: var(--ink-soft);
  }
</style>
</head>
<body>
  <section class="card card-front">
    <div class="front-wordmark">HearthMile</div>
  </section>

  <section class="card card-back">
    <div class="back-wordmark">HearthMile</div>
    <h1 class="holder-name">Marcus Pell</h1>
    <p class="holder-title">CEO</p>
    <div class="title-rule"></div>
    <div class="contact-row">
      <span class="contact-item">
        <svg viewBox="0 0 24 24" fill="none" stroke="#1a95d4" stroke-width="2" stroke-linejoin="round" aria-hidden="true">
          <path d="M5 3h4l2 5-2.5 1.5a11 11 0 0 0 6 6L16 13l5 2v4a2 2 0 0 1-2 2A17 17 0 0 1 3 5a2 2 0 0 1 2-2z"/>
        </svg>
        732-555-0182
      </span>
      <span class="contact-item">
        <svg viewBox="0 0 24 24" fill="none" stroke="#1a95d4" stroke-width="2" stroke-linejoin="round" aria-hidden="true">
          <rect x="2" y="5" width="20" height="14" rx="1"/>
          <path d="M2 6l10 7 10-7"/>
        </svg>
        email@hearthmile.example
      </span>
    </div>
    <p class="address">48 Birchwell Court, Suite 314, Fernbrook, NJ 07799</p>
    <p class="licences">NMLS 61947 • Company NMLS 274615</p>
  </section>
</body>
</html>
```